Award-winnning Estate Agent needs a premium version of their 'For Sale' board design

We need a premium option for our 'For Sale' board design. We have a standard board that is attached to this brief, but were are looking to have a premium design version that we will use when selling exclusive properties. Our company name is Harbourline Vale Estates and the name for this is exclusive selection is: 'The Harbourline Collection'. The design needs to work with our current brand, but have a distinctive PREMIUM feel to it. I have uploaded the barnd guidelines and also some of the exisisting logo variations. We do NOT need a new logo but feel free to play around with colours, fonts, sizes etc. for the sign.

Target Market(s)

Property buyers & house hunters

Industry/Entity Type

Real Estate - Residential Property

Font styles to use
Sans Serif

Requirements
Must have
• A premium fee, must be square design, must be easy to read when driving past the sign
Nice to have
• I'm open ot ideas

```html
<!DOCTYPE html>
<html lang="en">
<head>
<meta charset="utf-8">
<title>Harbourline Vale Estates – For Sale Board</title>
<link href="https://fonts.googleapis.com/css2?family=Inter:wght@400;600&family=Montserrat:wght@300;700;800;900&display=swap" rel="stylesheet">
<style>
  :root {
    --page-grey: #dedede;
    --brand-purple: #463076;
    --brand-purple-light: #5b41a0;
    --brand-cyan: #1dc0ff;
    --white: #ffffff;
    --ink: #1b1b1b;
  }
  * { margin: 0; padding: 0; box-sizing: border-box; }
  html, body {
    width: 974px;
    height: 1200px;
    overflow: hidden;
    background: var(--page-grey);
  }
  .canvas {
    position: relative;
    width: 974px;
    height: 1200px;
  }
  .board {
    position: absolute;
    left: 87px;
    top: 200px;
    width: 800px;
    height: 800px;
    background: var(--white);
    box-shadow: 0 6px 28px rgba(0, 0, 0, 0.22);
    overflow: hidden;
  }
  .board__panel {
    position: absolute;
    left: 0;
    top: 0;
    width: 800px;
    height: 644px;
    background: radial-gradient(ellipse at 75% 15%, #503783 0%, var(--brand-purple) 55%, #432d71 100%);
  }
  .board__divider {
    position: absolute;
    left: 0;
    width: 800px;
    height: 3px;
    background: var(--brand-purple-light);
  }
  .board__divider--upper { top: 634px; }
  .board__divider--lower { top: 641px; background: var(--brand-purple); }

  .brand-name {
    position: absolute;
    left: 0;
    width: 800px;
    top: 172px;
    text-align: center;
    font-family: "Inter", sans-serif;
    font-weight: 600;
    font-size: 36px;
    letter-spacing: -0.5px;
    color: var(--white);
  }

  .headline {
    position: absolute;
    left: 152px;
    font-family: "Montserrat", sans-serif;
    line-height: 1;
  }
  .headline--for {
    top: 227px;
    font-weight: 300;
    font-size: 152px;
    letter-spacing: -2px;
    color: var(--white);
  }
  .headline--sale {
    top: 353px;
    font-weight: 900;
    font-size: 178px;
    letter-spacing: -5px;
    color: var(--brand-cyan);
  }

  .collection {
    position: absolute;
    left: 152px;
    top: 525px;
    width: 500px;
    height: 45px;
    border-top: 1px solid rgba(255, 255, 255, 0.55);
    border-bottom: 1px solid rgba(255, 255, 255, 0.55);
    display: flex;
    align-items: center;
    justify-content: center;
    font-family: "Montserrat", sans-serif;
    font-weight: 700;
    font-size: 30px;
    letter-spacing: 0.6px;
    color: var(--white);
    white-space: nowrap;
  }

  .phone-pill {
    position: absolute;
    left: 114px;
    top: 610px;
    width: 572px;
    height: 74px;
    border-radius: 37px;
    background: var(--brand-cyan);
    border: 2px solid var(--white);
    display: flex;
    align-items: center;
    padding-left: 12px;
  }
  .phone-pill__icon {
    width: 58px;
    height: 58px;
    flex: none;
  }
  .phone-pill__number {
    margin-left: 14px;
    font-family: "Montserrat", sans-serif;
    font-weight: 800;
    font-size: 62px;
    letter-spacing: 1px;
    line-height: 1;
    color: var(--white);
  }

  .website {
    position: absolute;
    left: 0;
    top: 706px;
    width: 800px;
    text-align: center;
    font-family: "Montserrat", sans-serif;
    font-weight: 700;
    font-size: 31px;
    letter-spacing: 2.6px;
    color: var(--ink);
  }
</style>
</head>
<body>
  <main class="canvas">
    <section class="board" aria-label="For Sale board">
      <div class="board__panel"></div>
      <div class="board__divider board__divider--upper"></div>
      <div class="board__divider board__divider--lower"></div>

      <p class="brand-name">Harbourline Vale Estates</p>

      <h1 class="headline headline--for">FOR</h1>
      <p class="headline headline--sale">SALE</p>

      <p class="collection">THE HARBOURLINE COLLECTION</p>

      <div class="phone-pill">
        <svg class="phone-pill__icon" viewBox="0 0 58 58" aria-hidden="true">
          <circle cx="29" cy="29" r="29" fill="#463076"/>
          <path d="M21 17c1.5-1 3-.6 3.8.8l2.4 4.2c.7 1.3.4 2.6-.8 3.4l-1.6 1.1c1.1 2.9 3.3 5.5 6 7.1l1.3-1.4c1-1 2.4-1.1 3.5-.3l3.8 2.8c1.2.9 1.3 2.5.2 3.6l-1.8 1.8c-1.6 1.6-4.2 2-6.6.9-6.4-2.9-11.4-8.6-13.3-15.3-.7-2.4 0-4.8 1.6-6.1z" fill="#ffffff"/>
          <path d="M33 18a9 9 0 0 1 7 7M33 14a13 13 0 0 1 11 11" fill="none" stroke="#ffffff" stroke-width="1.8" stroke-linecap="round"/>
        </svg>
        <span class="phone-pill__number">01632 960418</span>
      </div>

      <p class="website">www.harbourlinevale.co.uk</p>
    </section>
  </main>
</body>
</html>
```